TPW other templates

1) Internal pages for the documents that we write. basically what will the pages inside look like. It should basically be a document with a header, a footer and a page number locator. It should include the following information: name of the report, date, TPW logo somehow, and version (draft, final etc). the information should be divided between header and footer. let me know if its unclear. As with everything it should work both in black and white and in color in case it is printed in black and white :-)
2) chapter dividers. This are the pages that you might have inside the report to separate sections. It should just have a page number, and chapter or section name. Simple, but again follow the same idea of the design that you created. It should be possible to have a picture in the divider, but it should not be a must. so in that sense we need to versions.
3) Business cards. Should include space for name, title, phone numbers (2 or 3), email, Skype, web page, and the company address which you have already.
4) a signature for emails. Basically the file that is glued to the bottom off all emails as a signature. Again it should include all the information in the business cards.

Not including any files since you have already designed others

```html
<!DOCTYPE html>
<html lang="en">
<head>
<meta charset="utf-8">
<title>TPW Business Card</title>
<link href="https://fonts.googleapis.com/css2?family=Quicksand:wght@400;500;700&display=swap" rel="stylesheet">
<style>
  :root{
    --bg:#d5e1e7;
    --card:#fbfbfb;
    --navy:#27409a;
    --sky:#3a9fc9;
    --text:#4a4f55;
    --band-a:#eef3f8;
    --band-b:#d3e2ee;
    --rule:#8fc6de;
    --sep:#9a9fa5;
  }
  *{box-sizing:border-box;margin:0;padding:0}
  html,body{width:1200px;height:1000px;overflow:hidden}
  body{background:var(--bg);font-family:"Quicksand",sans-serif;position:relative}
  .card{position:absolute;width:500px;height:290px;background:var(--card);
    box-shadow:0 6px 16px rgba(40,60,80,.18);overflow:hidden}
  .card--front{left:90px;top:170px}
  .card--back{left:610px;top:540px}

  .decor-band{position:absolute;left:30px;right:20px;top:95px;height:110px;
    background:linear-gradient(90deg,var(--band-a),var(--band-b));border-radius:4px}
  .front-mark{position:absolute;left:0;right:0;top:112px;text-align:center;
    font-weight:700;font-size:72px;letter-spacing:4px;color:var(--navy);line-height:1}

  .back-inner{position:absolute;inset:0;padding:32px 40px 0;text-align:center;color:var(--text)}
  .brand{font-weight:700;font-size:32px;letter-spacing:2px;color:var(--navy);line-height:1}
  .brand-tagline{font-size:7px;color:var(--navy);margin-top:3px;letter-spacing:.3px}
  .person-name{font-weight:500;font-size:20px;color:var(--sky);margin-top:16px;line-height:1.2}
  .person-title{font-size:12px;margin-top:2px}
  .divider{height:1px;background:var(--rule);margin:12px 20px 10px}
  .contact{font-size:11px;line-height:1.8;text-align:left;padding-left:20px}
  .contact-row{display:flex;align-items:center;gap:12px;white-space:nowrap}
  .contact-item{display:inline-flex;align-items:center;gap:5px}
  .sep{color:var(--sep)}
  .icon{width:10px;height:10px;flex:none}
</style>
</head>
<body>

<section class="card card--front" aria-label="Business card front">
  <div class="decor-band" role="img" aria-label="Soft pale blue brand decoration behind the company name"></div>
  <div class="front-mark">TPW</div>
</section>

<section class="card card--back" aria-label="Business card back">
  <div class="back-inner">
    <div class="brand">TPW</div>
    <div class="brand-tagline">Trusted Partner Works Norway</div>
    <div class="person-name">Erik Larsen</div>
    <div class="person-title">Managing Director</div>
    <div class="divider"></div>
    <div class="contact">
      <div class="contact-row">
        <span class="contact-item">
          <svg class="icon" viewBox="0 0 10 10"><path d="M5 .5a3 3 0 0 1 3 3C8 6 5 9.5 5 9.5S2 6 2 3.5a3 3 0 0 1 3-3z" fill="var(--sky)"/><circle cx="5" cy="3.5" r="1" fill="#fff"/></svg>
          Havnegata 12, 0150 Oslo, Norway
        </span>
      </div>
      <div class="contact-row">
        <span class="contact-item">
          <svg class="icon" viewBox="0 0 10 10"><path d="M2 1l2 2-1 1.2c.6 1.2 1.6 2.2 2.8 2.8L7 6l2 2-1.3 1.5C4.5 9.5.5 5.5.5 2.3z" fill="var(--sky)"/></svg>
          +47 22 41 00 10
        </span>
        <span class="sep">|</span><span>+47 22 41 00 11</span>
        <span class="sep">|</span><span>+47 22 41 00 12</span>
      </div>
      <div class="contact-row">
        <span class="contact-item">
          <svg class="icon" viewBox="0 0 10 10"><rect x=".5" y="2" width="9" height="6.5" rx="1" fill="var(--sky)"/><path d="M1 2.5l4 3 4-3" stroke="#fff" fill="none" stroke-width=".8"/></svg>
          post@tpw.no
        </span>
        <span class="contact-item">
          <svg class="icon" viewBox="0 0 10 10"><circle cx="5" cy="5" r="4.5" fill="var(--sky)"/><path d="M.8 5h8.4M5 .6c-2 2.6-2 6.2 0 8.8M5 .6c2 2.6 2 6.2 0 8.8" stroke="#fff" fill="none" stroke-width=".6"/></svg>
          www.tpw.no
        </span>
        <span class="contact-item">
          <svg class="icon" viewBox="0 0 10 10"><circle cx="5" cy="5" r="4.5" fill="var(--sky)"/></svg>
          Erik.Larsen
        </span>
      </div>
    </div>
  </div>
</section>

</body>
</html>
```